Business Card Design (NEW FILES)

ATTENTION: New vector files are available. Please update your design to reflect/use the new (better resolution) logo images.

Seeking a unique and professional business card design for a commercial drone photography/videography business. The layout should feature
the logo (attached) and include the following information:
Owen Tarrick
614-502-7738
www.skylarkreelworks.example
NRD Certified Remote Pilot

Owen Tarrick

```html
<!DOCTYPE html>
<html lang="en">
<head>
<meta charset="utf-8">
<title>Skylark Reelworks – Business Card</title>
<link href="https://fonts.googleapis.com/css2?family=Open+Sans:ital,wght@0,400;0,600;0,700;1,400&display=swap" rel="stylesheet">
<style>
  :root {
    --backdrop: #222222;
    --navy: #12163f;
    --orange: #e8894f;
    --white: #f5f5f5;
    --muted: #d8dae6;
  }
  * { box-sizing: border-box; margin: 0; padding: 0; }
  html, body { width: 1200px; height: 780px; overflow: hidden; background: var(--backdrop); font-family: "Open Sans", Arial, sans-serif; }
  .canvas { position: relative; width: 1200px; height: 780px; }

  .card {
    position: absolute; top: 236px;
    width: 540px; height: 308px;
    background: var(--navy);
    border-radius: 18px;
    overflow: hidden;
  }
  .card--front { left: 40px; }
  .card--back { left: 620px; }

  /* Front */
  .brand-name {
    position: absolute;
    color: var(--white);
    font-weight: 400;
    letter-spacing: 0.08em;
    text-transform: uppercase;
    line-height: 1.1;
  }
  .card--front .brand-name { left: 36px; top: 44px; font-size: 22px; }
  .card--front .brand-name .brand-line { display: block; }

  .divider {
    position: absolute; left: 262px; top: 78px;
    width: 2px; height: 150px; background: var(--orange);
  }

  .contact { position: absolute; left: 290px; top: 86px; color: var(--white); }
  .contact-name { font-size: 25px; font-weight: 700; line-height: 1.1; }
  .contact-name .first { color: var(--orange); }
  .contact-role { font-size: 13px; font-style: italic; color: var(--muted); margin-bottom: 10px; }
  .contact-cert { font-size: 12.5px; line-height: 1.45; }
  .contact-list { list-style: none; margin-top: 8px; font-size: 13px; line-height: 1.6; }
  .contact-list li { display: flex; align-items: center; gap: 8px; }
  .contact-list svg { width: 13px; height: 13px; flex: none; }

  .band { position: absolute; left: 0; bottom: 16px; height: 22px; }
  .band--orange { width: 200px; background: var(--orange); }
  .band--white { left: 200px; right: 0; background: var(--white); }
  .band-marker {
    position: absolute; left: 186px; bottom: 12px;
    width: 30px; height: 30px; border-radius: 50%;
    background: var(--navy); border: 3px solid var(--white);
  }

  /* Back */
  .card--back .brand-name {
    left: 0; right: 0; top: 118px; text-align: center; font-size: 34px;
  }
</style>
</head>
<body>
<main class="canvas">
  <section class="card card--front" aria-label="Business card front">
    <div class="brand-name"><span class="brand-line">Skylark</span><span class="brand-line">Reelworks</span></div>
    <div class="divider"></div>
    <div class="contact">
      <p class="contact-name"><span class="first">Owen</span> Tarrick</p>
      <p class="contact-role">Owner</p>
      <p class="contact-cert">NRD Certified Remote Pilot<br>Fully Insured</p>
      <ul class="contact-list">
        <li>
          <svg viewBox="0 0 24 24" aria-hidden="true"><path fill="#e8894f" d="M6.6 10.8a15 15 0 0 0 6.6 6.6l2.2-2.2c.3-.3.7-.4 1-.2 1.1.4 2.3.6 3.6.6.6 0 1 .4 1 1V20c0 .6-.4 1-1 1A17 17 0 0 1 3 4c0-.6.4-1 1-1h3.5c.6 0 1 .4 1 1 0 1.3.2 2.5.6 3.6.1.3 0 .7-.2 1z"/></svg>
          614-502-7738
        </li>
        <li>
          <svg viewBox="0 0 24 24" aria-hidden="true"><circle cx="12" cy="12" r="10" fill="#e8894f"/><path d="M2 12h20M12 2c3 3 3 17 0 20M12 2c-3 3-3 17 0 20" stroke="#12163f" stroke-width="1.6" fill="none"/></svg>
          www.skylarkreelworks.example
        </li>
        <li>
          <svg viewBox="0 0 24 24" aria-hidden="true"><rect x="2" y="5" width="20" height="14" rx="2" fill="#e8894f"/><path d="M3 6l9 7 9-7" stroke="#12163f" stroke-width="1.8" fill="none"/></svg>
          info@skylarkreelworks.example
        </li>
      </ul>
    </div>
    <div class="band band--orange"></div>
    <div class="band band--white"></div>
    <div class="band-marker"></div>
  </section>

  <section class="card card--back" aria-label="Business card back">
    <div class="brand-name">Skylark Reelworks</div>
  </section>
</main>
</body>
</html>
```